New Business Card Design Project

Use the flyer uploaded and website www.brightoakbuilders.com for inspiration.
List Our Services on Backside of business cards
Marcus Delling
Harborline Builders Inc.
Licensed General Contractors
858-471-6093

Contact Information for Business Card

Use the flyer uploaded and website www.brightoakbuilders.com for inspiration. List Our Services on Backside of business cards Marcus Delling Harborline Builders Inc. Licensed General Contractors 858-471-6093

```html
<!DOCTYPE html>
<html lang="en">
<head>
<meta charset="utf-8">
<title>Harborline Builders – Business Cards</title>
<link rel="stylesheet" href="https://fonts.googleapis.com/css2?family=Cinzel:wght@400;700&family=Montserrat:wght@400;500&display=swap">
<style>
  :root {
    --page-bg: #1d1d20;
    --card-bg: #131316;
    --card-edge: #2a2a2e;
    --ink: #f4f4f4;
    --ink-soft: #d9d9d9;
  }
  * { margin: 0; padding: 0; box-sizing: border-box; }
  html, body {
    width: 1200px; height: 912px; overflow: hidden;
    background: var(--page-bg);
  }
  .canvas { position: relative; width: 1200px; height: 912px; }
  .card {
    position: absolute;
    width: 560px; height: 320px;
    background: var(--card-bg);
    border: 1px solid var(--card-edge);
    border-radius: 16px;
    box-shadow: 0 18px 40px rgba(0,0,0,.55);
    color: var(--ink);
  }
  .card--front { left: 70px; top: 90px; }
  .card--back { left: 570px; top: 500px; }

  .brand-name {
    font-family: "Cinzel", serif;
    font-weight: 400;
    color: var(--ink);
    letter-spacing: 1px;
  }
  .card--front .brand-name {
    position: absolute; left: 0; right: 0; top: 108px;
    text-align: center; font-size: 30px;
  }
  .services {
    position: absolute; left: 0; right: 0; top: 200px;
    text-align: center;
    font-family: "Montserrat", sans-serif;
    font-size: 15px; line-height: 26px;
    color: var(--ink-soft);
  }

  .card--back .brand-name {
    position: absolute; left: 38px; top: 40px; font-size: 24px;
  }
  .person { position: absolute; left: 60px; top: 110px; }
  .person-name {
    font-family: "Cinzel", serif; font-weight: 700;
    font-size: 24px; letter-spacing: 1px;
  }
  .person-title {
    font-family: "Montserrat", sans-serif; font-size: 15px;
    color: var(--ink-soft); margin-top: 2px;
  }
  .contact-list {
    position: absolute; left: 60px; top: 182px;
    list-style: none;
    font-family: "Montserrat", sans-serif; font-size: 14px;
    color: var(--ink-soft);
  }
  .contact-list li { display: flex; align-items: center; gap: 10px; height: 24px; }
  .contact-list svg { width: 13px; height: 13px; fill: var(--ink); }
  .company-line {
    position: absolute; left: 60px; top: 270px;
    font-family: "Montserrat", sans-serif; font-size: 15px;
    color: var(--ink-soft);
  }
</style>
</head>
<body>
<main class="canvas">
  <section class="card card--front" aria-label="Card front">
    <h1 class="brand-name">Harborline Builders</h1>
    <p class="services">
      Painting • Flooring • Kitchens • Custom Renovations<br>
      Bathrooms • Energy Efficient Upgrades
    </p>
  </section>

  <section class="card card--back" aria-label="Card back">
    <h2 class="brand-name">Harborline Builders</h2>
    <div class="person">
      <p class="person-name">Marcus Delling</p>
      <p class="person-title">Licensed General Contractors</p>
    </div>
    <ul class="contact-list">
      <li>
        <svg viewBox="0 0 24 24" aria-hidden="true"><path d="M6.6 10.8a15 15 0 0 0 6.6 6.6l2.2-2.2a1 1 0 0 1 1-.25 11.4 11.4 0 0 0 3.6.57 1 1 0 0 1 1 1V20a1 1 0 0 1-1 1A17 17 0 0 1 3 4a1 1 0 0 1 1-1h3.5a1 1 0 0 1 1 1c0 1.25.2 2.45.57 3.57a1 1 0 0 1-.25 1z"/></svg>
        858-471-6093
      </li>
      <li>
        <svg viewBox="0 0 24 24" aria-hidden="true"><path d="M2 5h20v14H2z M3.5 6.5 12 13l8.5-6.5" fill="none" stroke="#f4f4f4" stroke-width="2"/></svg>
        info@brightoakbuilders.com
      </li>
      <li>
        <svg viewBox="0 0 24 24" aria-hidden="true"><circle cx="12" cy="12" r="10"/></svg>
        www.brightoakbuilders.com
      </li>
    </ul>
    <p class="company-line">Harborline Builders Inc.</p>
  </section>
</main>
</body>
</html>
```